Business Card Design for Occupational Medicine Start Up Company

We need to design a professional business card. We are a healthcare company providing occupational medicine services to blue collar industries. We are professional, efficient and high quality service providers.

Target Market(s)

Blue Collar Industry: Shipbuilding, Ports, Trucking Companies; The Executives and Safety Officers for these companies

Industry/Entity Type

Healthcare

Contact Information for Business Card

Logo, Name, Title, Email, Phone

Other font styles liked:
• Please match our Brand Guide

Requirements
Must have
• Our Company Colors and Logo

```html
<!DOCTYPE html>
<html lang="en">
<head>
<meta charset="utf-8">
<title>Crewline Clinics Business Card</title>
<link rel="stylesheet" href="https://fonts.googleapis.com/css2?family=Montserrat:wght@400;700&family=Roboto:wght@400&display=swap">
<style>
  :root {
    --navy: #1b2a8a;
    --navy-deep: #17237c;
    --sky: #2ea3e3;
    --gold: #f2b441;
    --paper: #ffffff;
    --ink: #1d1d1d;
    --backdrop: #e4e4e4;
  }
  * { margin: 0; padding: 0; box-sizing: border-box; }
  html, body { width: 1200px; height: 900px; overflow: hidden; }
  body {
    background: var(--backdrop);
    position: relative;
    font-family: "Montserrat", sans-serif;
  }
  .card {
    position: absolute;
    width: 600px;
    height: 343px;
    border-radius: 3px;
    overflow: hidden;
    box-shadow: 0 6px 18px rgba(0,0,0,0.18);
  }
  .card-back {
    left: 110px; top: 100px;
    background: var(--navy-deep);
  }
  .card-front {
    left: 490px; top: 470px;
    background: var(--paper);
  }
  .brand { position: absolute; display: flex; align-items: center; gap: 14px; }
  .brand-dot {
    width: 40px; height: 40px; border-radius: 50%;
    background: var(--sky);
    flex: none;
  }
  .brand-name {
    font-weight: 700;
    text-transform: uppercase;
    line-height: 1;
    display: flex; flex-direction: column; align-items: center;
  }
  .brand-name .word-main { font-size: 30px; letter-spacing: 0.5px; }
  .brand-name .word-sub { font-size: 15px; letter-spacing: 6px; margin-top: 4px; }
  .card-back .brand { left: 170px; top: 135px; }
  .card-back .brand-name { color: var(--paper); }
  .card-front .brand { left: 60px; top: 50px; }
  .card-front .brand-name { color: var(--navy); }
  .person {
    position: absolute; left: 250px; top: 160px;
  }
  .person-name {
    font-weight: 700; font-size: 26px; color: var(--navy); line-height: 1.1;
  }
  .person-title {
    font-family: "Roboto", sans-serif;
    font-size: 11px; color: var(--ink); margin-top: 2px;
  }
  .contacts {
    position: absolute; left: 250px; top: 218px;
    list-style: none;
    font-family: "Roboto", sans-serif; font-size: 14px; color: var(--ink);
  }
  .contacts li { display: flex; align-items: center; gap: 12px; height: 22px; }
  .contacts svg { width: 13px; height: 13px; fill: var(--navy); }
  .stripe-band {
    position: absolute; left: 0; bottom: 0; width: 600px; height: 60px;
    background: linear-gradient(to bottom, var(--gold) 0%, var(--navy) 50%, var(--sky) 100%);
    opacity: 0.9;
  }
</style>
</head>
<body>
  <section class="card card-back">
    <div class="brand">
      <span class="brand-dot"></span>
      <span class="brand-name"><span class="word-main">Crewline</span><span class="word-sub">Clinics</span></span>
    </div>
  </section>

  <section class="card card-front">
    <div class="brand">
      <span class="brand-dot"></span>
      <span class="brand-name"><span class="word-main">Crewline</span><span class="word-sub">Clinics</span></span>
    </div>

    <div class="person">
      <p class="person-name">Marisol</p>
      <p class="person-title">Manager</p>
    </div>

    <ul class="contacts">
      <li>
        <svg viewBox="0 0 24 24" aria-hidden="true"><path d="M6.6 10.8a15.1 15.1 0 006.6 6.6l2.2-2.2a1 1 0 011-.25 11.4 11.4 0 003.6.57 1 1 0 011 1V20a1 1 0 01-1 1A17 17 0 013 4a1 1 0 011-1h3.5a1 1 0 011 1c0 1.25.2 2.45.57 3.57a1 1 0 01-.25 1z"/></svg>
        555 210 4837
      </li>
      <li>
        <svg viewBox="0 0 24 24" aria-hidden="true"><path d="M2 5h20v14H2z M2 5l10 8 10-8" fill="none" stroke="#1b2a8a" stroke-width="2"/></svg>
        hello@crewlineclinics.com
      </li>
    </ul>

    <div class="stripe-band" role="img" aria-label="Decorative band in the brand colours gold, navy and sky blue"></div>
  </section>
</body>
</html>
```